Quorva - corporate Business Card

We need a good look and innovative business card for a new start up company based in Los Angeles called "Quorva". We are in a payment business, including payment card, app, and ewallet. We are expert in online payment and Card not present (CNP) transaction.
We need an innovative, modern business card.

Our logo font is Aero Matics

Target Market(s)

Startup - Bank - Online Payment - Card Manufacturing

Industry/Entity Type

Startup

Contact Information for Business Card

phone: 555 014 7396 - Address: 4172 Marlowe blvd, Linden Vale, CA 90299

Requirements
Must have
• Message: innovative, professional, expert, high tech, trust, online payment expert, security
Nice to have
• no comment
Should not have
• no Comment

```html
<!DOCTYPE html>
<html lang="en">
<head>
<meta charset="utf-8">
<title>Quorva – Business Card</title>
<link href="https://fonts.googleapis.com/css2?family=Ubuntu:wght@400;500;700&display=swap" rel="stylesheet">
<style>
  :root {
    --brand-red: #b81f2d;
    --card-white: #ffffff;
    --ring-white: #f7f7f7;
    --ink: #1e1e1e;
    --backdrop: #ececec;
    --shadow: rgba(0, 0, 0, 0.18);
  }
  * { margin: 0; padding: 0; box-sizing: border-box; }
  html, body {
    width: 1200px; height: 900px; overflow: hidden;
    background: var(--backdrop);
    font-family: "Ubuntu", sans-serif;
  }
  .canvas { position: relative; width: 1200px; height: 900px; }

  .card {
    position: absolute; width: 556px; height: 345px;
    border-radius: 18px; overflow: hidden;
    box-shadow: 0 6px 18px var(--shadow);
  }

  /* Front */
  .card-front { left: 238px; top: 60px; background: var(--card-white); }
  .front-band {
    position: absolute; left: 407px; top: 0; width: 149px; height: 100%;
    background: var(--brand-red);
  }
  .front-ring {
    position: absolute; left: 295px; top: 68px; width: 210px; height: 210px;
    border-radius: 50%; background: var(--ring-white);
    box-shadow: -6px 0 14px rgba(0,0,0,0.05);
  }
  .brand-disc {
    position: absolute; border-radius: 50%;
    display: flex; align-items: center; justify-content: center;
    font-weight: 700; letter-spacing: 0.5px;
  }
  .front-disc {
    left: 322px; top: 95px; width: 156px; height: 156px;
    background: var(--brand-red); color: var(--card-white); font-size: 28px;
  }
  .holder-name {
    position: absolute; left: 36px; top: 38px;
    font-size: 25px; font-weight: 700; color: var(--brand-red);
  }
  .holder-role {
    position: absolute; left: 37px; top: 66px;
    font-size: 17px; font-weight: 500; color: var(--ink); letter-spacing: 0.4px;
  }
  .contact-list {
    position: absolute; left: 37px; top: 197px; list-style: none;
    font-size: 16px; color: var(--ink);
  }
  .contact-item { display: flex; align-items: center; gap: 9px; height: 26px; }
  .contact-icon { width: 22px; height: 22px; flex: none; }
  .postal-address {
    position: absolute; left: 37px; top: 265px;
    font-size: 15.5px; line-height: 21px; color: var(--ink); font-style: normal;
  }

  /* Back */
  .card-back { left: 457px; top: 522px; background: var(--brand-red); }
  .back-disc {
    left: 190px; top: 82px; width: 180px; height: 180px;
    background: var(--ring-white); color: var(--brand-red); font-size: 30px;
    box-shadow: 0 2px 4px rgba(0,0,0,0.35);
  }
</style>
</head>
<body>
<main class="canvas">

  <section class="card card-front" aria-label="Business card front">
    <div class="front-band"></div>
    <div class="front-ring"></div>
    <div class="brand-disc front-disc">Quorva</div>

    <h1 class="holder-name">Dana Whitlock</h1>
    <p class="holder-role">Director</p>

    <ul class="contact-list">
      <li class="contact-item">
        <svg class="contact-icon" viewBox="0 0 22 22" aria-hidden="true">
          <circle cx="11" cy="11" r="11" fill="#b81f2d"/>
          <rect x="7.5" y="5" width="7" height="12" rx="1.3" fill="none" stroke="#fff" stroke-width="1.4"/>
          <circle cx="11" cy="14.8" r="0.9" fill="#fff"/>
        </svg>
        <span>555 014 7396</span>
      </li>
      <li class="contact-item">
        <svg class="contact-icon" viewBox="0 0 22 22" aria-hidden="true">
          <circle cx="11" cy="11" r="11" fill="#b81f2d"/>
          <circle cx="11" cy="11" r="5.5" fill="none" stroke="#fff" stroke-width="1.3"/>
          <path d="M5.5 11h11M11 5.5c-2.2 2.6-2.2 8.4 0 11M11 5.5c2.2 2.6 2.2 8.4 0 11" fill="none" stroke="#fff" stroke-width="1.1"/>
        </svg>
        <span>www.quorva.com</span>
      </li>
    </ul>

    <address class="postal-address">4172 Marlowe blvd,<br>Linden Vale, CA 90299</address>
  </section>

  <section class="card card-back" aria-label="Business card back">
    <div class="brand-disc back-disc">Quorva</div>
  </section>

</main>
</body>
</html>
```